Upmarket Dessert Lounge needs a Business Card Design

We are an upmarket dessert lounge needing a business card to match our image.

We want something that is simple yet beautiful, feminine, classy, sophisticated and elegant. We want it to stand out and don't mind if it is bold.

The design should include our logo and colours of red or maroon with gold highlights. We don't mind if black is used.

Marlow & Quince

Target Market(s)

For those who like to indulge or treat themselves and give in to their temptations on good quality desserts.

Industry/Entity Type

Business

Requirements
Must have
• Must include our logo and our name

Marlow & Quince

M & Q

```html
<!DOCTYPE html>
<html lang="en">
<head>
<meta charset="utf-8">
<title>Marlow &amp; Quince – Business Card</title>
<link rel="stylesheet" href="https://fonts.googleapis.com/css2?family=Tinos:wght@400;700&display=swap">
<style>
  :root {
    --maroon: #7a1a1f;
    --maroon-deep: #5e1216;
    --gold: #f2c99a;
    --peach: #f6cfa6;
    --ink: #111111;
    --text-grey: #555555;
    --paper: #ffffff;
    --blush: #ead9da;
    --backdrop: #e9e6e2;
  }
  * { margin: 0; padding: 0; box-sizing: border-box; }
  html, body { width: 1200px; height: 417px; overflow: hidden; }
  body {
    background: var(--backdrop);
    font-family: "Tinos", "Times New Roman", serif;
    position: relative;
  }
  .card {
    position: absolute;
    width: 515px;
    height: 294px;
    background: var(--paper);
    border-radius: 13px;
    overflow: hidden;
  }
  .card--front { left: 64px; top: 61px; }
  .card--back { left: 621px; top: 62px; width: 513px; }

  .brand-name {
    position: absolute;
    font-family: "Tinos", "Times New Roman", serif;
    font-weight: 400;
    color: var(--maroon);
    letter-spacing: 1px;
    white-space: nowrap;
    text-transform: uppercase;
  }
  .card--front .brand-name { left: 40px; top: 100px; width: 260px; text-align: center; font-size: 24px; }
  .card--back .brand-name { left: 0; top: 130px; width: 100%; text-align: center; font-size: 26px; }

  .contact {
    position: absolute;
    left: 338px;
    top: 56px;
    font-size: 13.5px;
    line-height: 20px;
    color: var(--text-grey);
    list-style: none;
  }
  .contact .address { margin-bottom: 4px; }
  .contact li { display: flex; align-items: center; }
  .contact svg { width: 10px; height: 10px; margin-right: 7px; fill: var(--maroon); flex: none; }

  .wave { position: absolute; left: 0; top: 0; width: 515px; height: 294px; }

  .holder {
    position: absolute;
    left: 337px;
    top: 233px;
    color: var(--gold);
    font-size: 17px;
    font-weight: 700;
    white-space: nowrap;
  }
  .holder .title { font-size: 13px; font-weight: 400; }
  .holder-flourish {
    position: absolute;
    left: 337px;
    top: 259px;
    width: 152px;
    height: 22px;
    background: linear-gradient(90deg, transparent, var(--maroon) 20%, var(--maroon) 80%, transparent);
    opacity: 0.85;
  }

  .border-pattern {
    position: absolute;
    left: 0;
    width: 100%;
    height: 36px;
    background: linear-gradient(180deg, var(--blush), #f3e9ea);
  }
  .border-pattern--top { top: 0; }
  .border-pattern--bottom { bottom: 0; background: linear-gradient(0deg, var(--blush), #f3e9ea); }
</style>
</head>
<body>

<section class="card card--front">
  <div class="brand-name">Marlow &amp; Quince</div>

  <ul class="contact">
    <li class="address">00, Complex name<br>City, State 000 000</li>
    <li><svg viewBox="0 0 10 10"><path d="M2 0.5l2 2-1 1.2c.6 1.3 1.6 2.3 2.9 2.9l1.2-1 2 2-1.3 1.8C4.5 9.2.8 5.5.5 1.8z"/></svg>+234 801 555 0142</li>
    <li><svg viewBox="0 0 10 10"><rect x="2" y="0" width="6" height="10" rx="1"/><rect x="3" y="1.5" width="4" height="4" fill="#fff"/></svg>+234 801 555 0142</li>
    <li><svg viewBox="0 0 10 10"><rect x="0" y="2" width="10" height="6.5" rx="0.5"/><path d="M0.5 2.5L5 6l4.5-3.5" stroke="#fff" stroke-width="0.9" fill="none"/></svg>hello@marlowquince.com</li>
    <li><svg viewBox="0 0 10 10"><circle cx="5" cy="5" r="4.8"/><path d="M0.5 5h9M5 0.3v9.4" stroke="#fff" stroke-width="0.7"/></svg>www.marlowquince.com</li>
  </ul>

  <svg class="wave" viewBox="0 0 515 294" aria-hidden="true">
    <path d="M0 196 C60 230 140 252 230 238 C320 224 420 186 515 186 L515 294 L0 294 Z" fill="var(--maroon)"/>
    <path d="M0 202 C60 236 140 258 230 244 C320 230 420 192 515 192 L515 294 L0 294 Z" fill="var(--paper)"/>
    <path d="M0 206 C60 240 140 262 230 248 C320 234 420 196 515 196 L515 294 L0 294 Z" fill="var(--ink)"/>
    <path d="M0 212 C50 244 110 262 170 266 C250 256 380 214 515 203 L515 294 L0 294 Z" fill="var(--peach)"/>
    <path d="M0 218 C50 250 110 268 160 270 C250 262 380 222 515 210 L515 294 L0 294 Z" fill="var(--ink)"/>
  </svg>

  <div class="holder">YOUR NAME, <span class="title">Title</span></div>
  <div class="holder-flourish" role="img" aria-label="Decorative flourish under the name"></div>
</section>

<section class="card card--back">
  <div class="border-pattern border-pattern--top" role="img" aria-label="Soft blush ornamental border"></div>
  <div class="brand-name">Marlow &amp; Quince</div>
  <div class="border-pattern border-pattern--bottom" role="img" aria-label="Soft blush ornamental border"></div>
</section>

</body>
</html>
```